WP website design (Harrowgate)

We need a wordpress design for an established auction and real estate company based in Florida. The winning design will incorporate a professional color scheme with company logo in a clean layout. The design needs to consider that this will be developed on a responsive theme. Colors are those that will highlight the logo.

Industry/Entity Type

Real Estate

Font styles to use
Serif
Sans Serif

Colors

Designer to choose colors to be used in the design.

Requirements
Must have
• Navigation:
1) Home
2) Auctions
3) Online Auctions
4) About Us
5) Services
6) Real Estate Listings
7) References
8) Contact Us

Colors will be blue (#000066) / red (#B10000) and black or other complementary color. Tagline to be used "Since 1977, Proven Results." Slideshow to be placed in the header or body of home page - please use stock real estate image.

Widgets: 1) Email Sign-up 2) Social media icons for FB and LinkedIn 3) Featured Listings 4) Testimonials 5) Register button

Footer will have smaller company logo, attached logos and contact info:
Phone: (555) 261-0948 Mobile: (555) 718-3062
Email: mirelharrowgate@quellmail.example
Address: 58 E. Tamsin Avenue, Ste 410, Pensacola, FL 32599
Nice to have
• Use of a drop down menu:
Auctions-
1) Upcoming Auctions
2) Past Auctions

```html
<!DOCTYPE html>
<html lang="en">
<head>
<meta charset="utf-8">
<title>Harrowgate Auctions – Home</title>
<link href="https://fonts.googleapis.com/css2?family=Oswald:wght@400;500;600&family=Open+Sans:wght@400;600;700&display=swap" rel="stylesheet">
<style>
:root{
  --navy:#000066;
  --red:#b10000;
  --red-bright:#d0111b;
  --ink:#333;
  --muted:#777;
  --nav:#2a2a2a;
  --footer:#1e2126;
  --footer-deep:#15171b;
  --line:#e2e2e2;
  --white:#fff;
}
*{box-sizing:border-box;margin:0;padding:0}
html,body{width:1200px;height:2252px;overflow:hidden}
body{font-family:"Open Sans",Arial,sans-serif;color:var(--ink);background:var(--white);font-size:13px}
.container{width:960px;margin:0 auto;position:relative}
.heading{font-family:"Oswald","Arial Narrow",sans-serif}

/* header */
.site-header{height:148px}
.site-header .container{height:148px}
.brand{position:absolute;left:0;top:46px;display:flex;align-items:center;gap:12px}
.brand-mark{width:44px;height:44px;background:var(--red)}
.brand-name{font-family:"Oswald",sans-serif;font-weight:600;font-size:34px;color:var(--navy);letter-spacing:.5px}
.utility{position:absolute;right:0;top:16px;display:flex;gap:22px;font-size:12px;color:var(--muted);align-items:center}
.utility span{display:flex;align-items:center;gap:6px}
.utility i{width:10px;height:10px;background:var(--red);display:inline-block;border-radius:2px}
.search{position:absolute;right:0;top:64px;width:260px;height:34px;border:1px solid #ccc;border-radius:3px;display:flex;align-items:center;justify-content:space-between;padding:0 10px;color:#999;font-size:12px}

/* nav */
.main-nav{background:var(--nav);height:42px}
.main-nav ul{list-style:none;display:flex;height:42px}
.main-nav li{color:var(--white);font-family:"Oswald",sans-serif;font-size:14px;letter-spacing:.5px;padding:0 20px;line-height:42px;position:relative}
.main-nav li.active{background:var(--red)}
.dropdown{position:absolute;left:0;top:42px;width:200px;background:var(--red);z-index:5}
.dropdown div{font-family:"Open Sans",sans-serif;font-size:12px;line-height:40px;padding:0 16px;border-bottom:1px solid rgba(255,255,255,.25);letter-spacing:0}

/* hero */
.hero{position:relative;height:380px;overflow:hidden}
.hero-photo{position:absolute;inset:0;background:linear-gradient(100deg,#6e6259 0%,#a59686 30%,#d8cdbf 55%,#b8a896 75%,#7a6c60 100%)}
.hero-shade{position:absolute;inset:0;background:rgba(0,0,0,.18)}
.hero-text{position:absolute;left:0;right:0;top:180px;text-align:center;color:var(--white)}
.hero-text h1{font-family:"Oswald",sans-serif;font-weight:500;font-size:52px;letter-spacing:1px}
.hero-text p{font-family:"Oswald",sans-serif;font-size:17px;letter-spacing:1px;margin-top:6px}
.hero-arrow{position:absolute;top:170px;width:40px;height:40px;border-radius:50%;background:rgba(255,255,255,.35)}
.hero-arrow.left{left:24px}.hero-arrow.right{right:24px}
.hero-arrow svg{position:absolute;left:12px;top:12px}

/* welcome */
.welcome{height:250px;text-align:center;padding-top:36px}
.section-title{font-family:"Oswald",sans-serif;color:var(--red);font-size:28px;font-weight:500}
.welcome p{width:900px;margin:18px auto 0;font-size:13px;line-height:22px;color:var(--muted)}
.btn{display:inline-block;background:var(--nav);color:var(--white);font-family:"Oswald",sans-serif;font-size:14px;letter-spacing:.5px;padding:0 26px;line-height:38px;border-radius:3px}
.welcome .btn{margin-top:24px}

/* featured */
.featured{height:510px;padding-top:20px}
.featured-head{display:flex;justify-content:space-between;align-items:center;border-bottom:1px solid var(--line);padding-bottom:10px}
.featured-head .section-title{font-size:20px}
.pager{display:flex;gap:4px}
.pager span{width:22px;height:22px;border:1px solid #ccc;display:block}
.cards{display:flex;gap:30px;margin-top:22px}
.card{width:300px}
.card-photo{position:relative;height:210px}
.card-photo .fill{position:absolute;inset:0}
.badge{position:absolute;right:0;top:0;width:110px;background:var(--navy);color:var(--white);font-size:12px;text-align:center;padding:6px 0}
.badge b{display:block;background:var(--red);font-size:14px;padding:4px 0;margin-top:4px}
.meta{display:flex;justify-content:space-between;font-size:11px;color:var(--muted);padding:8px 4px;border-bottom:1px solid var(--line)}
.meta span{display:flex;align-items:center;gap:5px}
.meta i{width:10px;height:10px;border:1px solid #999;display:inline-block}
.card h3{color:var(--red);font-size:14px;font-weight:700;margin-top:12px}
.card p{font-size:12px;line-height:19px;color:var(--muted);margin-top:8px}
.card .btn{font-size:12px;line-height:30px;padding:0 16px;margin-top:14px}

/* testimonial */
.testimonial{height:330px;border-top:1px solid var(--line);border-bottom:1px solid var(--line)}
.testimonial .container{height:330px}
.person{position:absolute;left:40px;top:30px;width:170px;text-align:center}
.portrait{width:170px;height:170px;border-radius:50%;border:6px solid #eee;background:linear-gradient(160deg,#c9b7a8,#7e6a5c)}
.person h4{font-family:"Oswald",sans-serif;color:var(--red);font-weight:400;font-size:18px;margin-top:26px;letter-spacing:.5px}
.quote{position:absolute;left:270px;top:44px;width:680px;font-size:12.5px;line-height:22px;color:var(--muted)}
.quote-mark{font-family:Georgia,serif;font-size:44px;color:#555;position:absolute;line-height:1}
.quote-mark.open{left:244px;top:34px}
.quote-mark.close{left:920px;top:210px}

/* partners */
.partners{height:130px}
.partners .container{display:flex;justify-content:space-between;align-items:center;height:130px;padding:0 20px}
.partner{width:130px;height:52px;border-radius:3px}

/* footer */
.site-footer{background:var(--footer);height:452px;color:#bbb;position:relative}
.footer-cols{display:flex;gap:50px;padding-top:40px}
.footer-col{width:290px}
.footer-col h5{font-family:"Oswald",sans-serif;color:var(--white);font-weight:400;font-size:20px;margin-bottom:16px}
.footer-col p{font-size:12px;line-height:21px}
.contact-row{display:flex;gap:10px;font-size:12px;line-height:19px;margin-bottom:12px}
.contact-row svg{flex:none;margin-top:3px}
.email-field{margin-top:16px;height:36px;background:var(--white);color:#999;font-size:12px;line-height:36px;padding:0 12px;border-radius:2px}
.submit{margin-top:12px;display:inline-block;background:var(--red-bright);color:var(--white);font-family:"Oswald",sans-serif;font-size:14px;line-height:36px;padding:0 30px;border-radius:2px}
.footer-bar{position:absolute;left:0;right:0;bottom:0;height:80px;background:var(--footer-deep)}
.footer-bar .container{display:flex;justify-content:space-between;align-items:center;height:80px;font-size:12px}
.social{display:flex;gap:8px}
.social span{width:26px;height:26px;border-radius:50%;background:#3a3e45;display:block}
</style>
</head>
<body>

<header class="site-header">
  <div class="container">
    <div class="brand"><span class="brand-mark"></span><span class="brand-name">Harrowgate Auctions</span></div>
    <div class="utility">
      <span><i></i>Client Login</span>
      <span><i></i>Register Here</span>
      <span><i></i>Call: (555) 261-0948</span>
    </div>
    <div class="search">Enter keywords...
      <svg width="14" height="14" viewBox="0 0 14 14"><circle cx="6" cy="6" r="4.5" fill="none" stroke="#888" stroke-width="1.5"/><line x1="9.5" y1="9.5" x2="13" y2="13" stroke="#888" stroke-width="1.5"/></svg>
    </div>
  </div>
</header>

<nav class="main-nav">
  <div class="container">
    <ul>
      <li>HOME</li>
      <li class="active">AUCTIONS
        <div class="dropdown"><div>Upcoming Auctions</div><div>Past Auctions</div></div>
      </li>
      <li>ONLINE AUCTIONS</li>
      <li>ABOUT US</li>
      <li>SERVICES</li>
      <li>REAL ESTATE LISTINGS</li>
      <li>REFERENCES</li>
      <li>CONTACT US</li>
    </ul>
  </div>
</nav>

<section class="hero">
  <div class="hero-photo" role="img" aria-label="Bright furnished living room with sofa and large windows"></div>
  <div class="hero-shade"></div>
  <div class="hero-arrow left"><svg width="16" height="16" viewBox="0 0 16 16"><polyline points="10,2 4,8 10,14" fill="none" stroke="#fff" stroke-width="2"/></svg></div>
  <div class="hero-arrow right"><svg width="16" height="16" viewBox="0 0 16 16"><polyline points="6,2 12,8 6,14" fill="none" stroke="#fff" stroke-width="2"/></svg></div>
  <div class="hero-text">
    <h1>SINCE 1977, PROVEN RESULTS</h1>
    <p>NEQUE PORRO QUISQUAM EST QUI DOLOREM IPSUM QUIA DOLOR SIT AMET</p>
  </div>
</section>

<section class="welcome">
  <h2 class="section-title">Welcome To Our Company</h2>
  <p>For more than four decades our team has guided buyers and sellers across Florida through auctions and private sales. We combine local market knowledge with a proven marketing process, so every property reaches serious bidders and every client receives clear advice, honest valuations and a result worth the wait. From family homes to commercial land, we handle each sale with care.</p>
  <span class="btn">FIND THE HOME</span>
</section>

<section class="featured">
  <div class="container">
    <div class="featured-head">
      <h2 class="section-title">Featured Listings</h2>
      <div class="pager"><span></span><span></span></div>
    </div>
    <div class="cards">
      <article class="card">
        <div class="card-photo">
          <div class="fill" role="img" aria-label="Exterior of a waterfront house" style="background:linear-gradient(180deg,#9fb4c6,#6b7a70)"></div>
          <div class="badge">Commercial<b>$ 500,000</b></div>
        </div>
        <div class="meta"><span><i></i>1540 Sq Ft</span><span><i></i>3 Bedrooms</span><span><i></i>2 Bathrooms</span></div>
        <h3>Waterfront home with private boat dock</h3>
        <p>Spacious rooms, updated finishes and a quiet street close to schools, shops and the beach.</p>
        <span class="btn">View Details</span>
      </article>
      <article class="card">
        <div class="card-photo">
          <div class="fill" role="img" aria-label="Interior of a furnished office suite" style="background:linear-gradient(180deg,#d9cbb8,#8d7761)"></div>
          <div class="badge">Commercial<b>$ 500,000</b></div>
        </div>
        <div class="meta"><span><i></i>2210 Sq Ft</span><span><i></i>4 Bedrooms</span><span><i></i>3 Bathrooms</span></div>
        <h3>Downtown office suite near the bay</h3>
        <p>Open layout, modern lighting and easy parking a short walk from cafes, banks and the harbor.</p>
        <span class="btn">View Details</span>
      </article>
      <article class="card">
        <div class="card-photo">
          <div class="fill" role="img" aria-label="Bedroom in a coastal villa" style="background:linear-gradient(180deg,#e6ddd2,#9c8a78)"></div>
          <div class="badge">Commercial<b>$ 500,000</b></div>
        </div>
        <div class="meta"><span><i></i>1875 Sq Ft</span><span><i></i>3 Bedrooms</span><span><i></i>2 Bathrooms</span></div>
        <h3>Bright coastal villa with open kitchen</h3>
        <p>Large windows, fresh paint and a shaded patio only minutes from parks, dining and the shore.</p>
        <span class="btn">View Details</span>
      </article>
    </div>
  </div>
</section>

<section class="testimonial">
  <div class="container">
    <div class="person">
      <div class="portrait" role="img" aria-label="Portrait of a satisfied client"></div>
      <h4>DORIAN WELCOTT</h4>
    </div>
    <span class="quote-mark open">&ldquo;</span>
    <p class="quote">Working with this team was the easiest sale we have ever made. They explained every step of the auction, set a fair reserve and brought in a crowd of qualified buyers. The house sold on the first day for more than we hoped. Their staff answered every call quickly and kept us informed from the first visit to the closing table. We recommend them to any family or business owner who wants a fast, fair and professional result.</p>
    <span class="quote-mark close">&rdquo;</span>
  </div>
</section>

<section class="partners">
  <div class="container">
    <span class="partner" style="background:#d7d7d7"></span>
    <span class="partner" style="background:#b9d3a6"></span>
    <span class="partner" style="background:#b7c6d8"></span>
    <span class="partner" style="background:#9aa6c4"></span>
    <span class="partner" style="background:#d8b7b7"></span>
  </div>
</section>

<footer class="site-footer">
  <div class="container footer-cols">
    <div class="footer-col">
      <h5>About Us</h5>
      <p>Serving Florida since 1977, we run public and online auctions for homes, land and commercial property. Our licensed team handles marketing, bidding and closing.</p>
    </div>
    <div class="footer-col">
      <h5>Contact Us</h5>
      <div class="contact-row">
        <svg width="12" height="16" viewBox="0 0 12 16"><path d="M6 1a5 5 0 0 0-5 5c0 4 5 9 5 9s5-5 5-9a5 5 0 0 0-5-5z" fill="#bbb"/><circle cx="6" cy="6" r="2" fill="#1e2126"/></svg>
        <span>58 E. Tamsin Avenue, Ste 410,<br>Pensacola, FL 32599</span>
      </div>
      <div class="contact-row">
        <svg width="14" height="14" viewBox="0 0 14 14"><path d="M3 1l2 3-1.5 1.5a8 8 0 0 0 5 5L10 9l3 2-1 2.5C6 13 1 8 .5 2z" fill="#bbb"/></svg>
        <span>Phone: (555) 261-0948<br>Mobile: (555) 718-3062</span>
      </div>
      <div class="contact-row">
        <svg width="14" height="12" viewBox="0 0 14 12"><rect x="1" y="1" width="12" height="10" fill="none" stroke="#bbb" stroke-width="1.4"/><polyline points="1,1 7,7 13,1" fill="none" stroke="#bbb" stroke-width="1.4"/></svg>
        <span>Email: mirelharrowgate@quellmail.example</span>
      </div>
    </div>
    <div class="footer-col">
      <h5>News Letters</h5>
      <p>Join our mailing list to hear about upcoming auctions and new listings before anyone else.</p>
      <div class="email-field">Enter Your Email</div>
      <span class="submit">SUBMIT</span>
    </div>
  </div>
  <div class="footer-bar">
    <div class="container">
      <span>Copyright 2014 Harrowgate. All Rights Reserved.</span>
      <div class="social"><span></span><span></span></div>
    </div>
  </div>
</footer>

</body>
</html>
```